Existing Website Requiring new Pages

I have an existing word press website that was built using elementor.
Website: www.tallowcrestcare.com.au
I require the Vacancies page (https://www.tallowcrestcare.com.au/vacancies/) to be modified to display our new properties along with minor tweaks to how the information is presented.
The vacancies to be displayed are the exactly the same as those that are located on the homepage of QMR website (https://qmr.org.au/)
The new pages that link off the Vacancies tab will require custom design.
There are roughly 8 pages/properties to be incorporated. i wish for the design to be very similar to that displayed in the following link; https://www.polunda.com.au/vacancies/merrylands
Along with this the back end has not been updated for the last 3 years so it also requires some maintenance.
Website is in the disability industry and the custom pages will display information relative to Property Vacancies.
I have attached a ZIP file with some design guides, the information for each of the properties (which will need to be modified to show our business name Tallowcrest Care) and the example of how it is to look based off the Polunda website.
If you guys have any suggestions or ideas on how to make this more presentable or possible i'm open to your ideas.
Target Market(s)
People looking for SDA properties custom built for people with a disability
Industry/Entity Type
Disability
Coding
Coded - Design and coding required
Number of Pages Required
5+ page

```html
<!DOCTYPE html>
<html lang="en">
<head>
<meta charset="utf-8">
<title>Vacancies – Tallowcrest Care</title>
<link href="https://fonts.googleapis.com/css2?family=Montserrat:wght@400;500;600;700;800&family=Inter:wght@400&display=swap" rel="stylesheet">
<style>
:root{
  --ink:#1f1f1f;
  --nav:#333333;
  --accent:#ee7d5b;
  --teal:#16d0b2;
  --pink-a:#df229f;
  --pink-b:#f7286a;
  --muted:#8a8a8a;
  --rule:#e5e5e5;
  --border:#d9d9d9;
  --footer-bar:#1b1b1b;
  --blue:#2b8fe0;
}
*{box-sizing:border-box;margin:0;padding:0}
html,body{width:1200px;height:2314px;overflow:hidden;background:#fff}
body{position:relative;font-family:"Montserrat",sans-serif;color:var(--ink)}
.abs{position:absolute}

/* header */
.brand{left:103px;top:40px;display:flex;align-items:center;gap:8px}
.brand-dot{width:16px;height:16px;border-radius:50%;background:var(--pink-b)}
.brand-name{font-size:22px;font-weight:600;color:#555;letter-spacing:.5px}
.main-nav{top:63px;left:576px;display:flex;gap:0;font-size:11.5px;font-weight:600;letter-spacing:.6px;color:var(--nav)}
.main-nav a{color:inherit;text-decoration:none;position:absolute;white-space:nowrap}
.main-nav .current{color:var(--accent)}

/* hero */
.hero{left:0;top:140px;width:1200px;height:480px;overflow:hidden}
.hero-photo{position:absolute;inset:0;background:linear-gradient(100deg,#d9dadc 0%,#eceded 40%,#c9cbcb 70%,#e2e3e3 100%)}
.hero-shape{position:absolute;left:0;top:0}
.hero-title{position:absolute;left:101px;top:202px;font-size:43px;font-weight:800;color:#fff;letter-spacing:.5px}

/* cards */
.card{width:321px;height:353px;border:1px solid var(--border);background:#fff}
.card-photo{position:absolute;left:6px;top:6px;width:309px;height:224px}
.card-title{position:absolute;left:22px;top:244px;font-size:23px;font-weight:700;color:var(--ink);display:flex;align-items:center;gap:4px}
.card-meta{position:absolute;left:22px;top:292px;font-size:16px;font-weight:400;color:#333;display:flex;align-items:center;gap:10px}
.card.is-active{border:none;box-shadow:0 0 10px rgba(0,0,0,.12)}
.card.is-active .card-title{color:var(--teal)}
.card.is-active::after{content:"";position:absolute;left:0;right:0;bottom:-4px;height:4px;background:var(--teal)}

/* footer */
.site-footer{left:0;top:1933px;width:1200px;height:310px;background:linear-gradient(#f4f4f4,#fff 30px)}
.footer-brand{left:79px;top:2030px;display:flex;align-items:center;gap:8px}
.footer-brand .brand-name{font-size:26px}
.footer-brand .brand-dot{width:20px;height:20px}
.contact-list{left:74px;top:2148px;font-size:13.5px;color:var(--muted);line-height:23.5px;list-style:none}
.contact-list li{display:flex;align-items:center;gap:8px}
.social{left:516px;top:1991px;list-style:none}
.social li{width:36px;height:36px;border-radius:50%;margin-bottom:8px}
.footer-col{width:244px}
.footer-col h4{font-size:16px;font-weight:500;color:var(--ink);border-left:3px solid var(--blue);padding-left:14px;margin-left:0;line-height:16px;margin-bottom:14px}
.footer-col ul{list-style:none}
.footer-col li{font-size:13.5px;color:var(--muted);border-bottom:1px solid var(--rule);padding:8px 0 8px;line-height:24px}
.bottom-bar{left:0;top:2243px;width:1200px;height:71px;background:var(--footer-bar);color:#fff;font-family:"Inter",sans-serif;font-size:13.5px}
.bottom-bar .copy{position:absolute;left:0;right:0;top:27px;text-align:center}
.bottom-bar .code{position:absolute;left:1104px;top:30px;font-size:9px}
.to-top{position:absolute;left:1155px;top:14px;width:45px;height:43px;background:#2a2a2a;display:flex;align-items:center;justify-content:center}
</style>
</head>
<body>

<header>
  <div class="abs brand"><span class="brand-dot"></span><span class="brand-name">Tallowcrest Care</span></div>
  <nav class="abs main-nav">
    <a style="left:0">HOME</a>
    <a style="left:62px">ABOUT US</a>
    <a class="current" style="left:151px">WHAT WE DO ⌄</a>
    <a style="left:277px">REFERRALS</a>
    <a style="left:374px">FEEDBACK</a>
    <a style="left:466px">CONTACT US</a>
  </nav>
</header>

<section class="abs hero">
  <div class="hero-photo" role="img" aria-label="Photo of a smiling woman in a wheelchair using a laptop while a carer leans over to help"></div>
  <svg class="hero-shape" width="600" height="480" viewBox="0 0 600 480">
    <defs>
      <linearGradient id="heroPink" x1="0" x2="1">
        <stop offset="0" stop-color="#df229f"/>
        <stop offset="1" stop-color="#f7286a"/>
      </linearGradient>
    </defs>
    <path d="M0 0 H340 A236 236 0 0 1 340 478 H0 Z" fill="#fff"/>
    <path d="M0 6 H330 A233 233 0 0 1 330 478 H0 Z" fill="url(#heroPink)"/>
  </svg>
  <h1 class="hero-title">VACANCIES</h1>
</section>

<main>
  <!-- row 1 -->
  <article class="abs card" style="left:104px;top:739px">
    <div class="card-photo" role="img" aria-label="Photo of a single-storey brick home with a garage and hedges in Penrith" style="background:linear-gradient(#dfe4ea,#8a7c6e 55%,#5f7a45)"></div>
    <h3 class="card-title"><svg width="12" height="16" viewBox="0 0 12 16"><path d="M6 0a6 6 0 0 0-6 6c0 4.5 6 10 6 10s6-5.5 6-10a6 6 0 0 0-6-6z" fill="currentColor"/><circle cx="6" cy="6" r="2.3" fill="#fff"/></svg>Penrith</h3>
    <p class="card-meta"><svg width="26" height="22" viewBox="0 0 26 22" fill="none" stroke="#f29b7a" stroke-width="1.5"><rect x="3" y="2" width="20" height="9" rx="1"/><rect x="6" y="5" width="6" height="4"/><rect x="14" y="5" width="6" height="4"/><rect x="1" y="11" width="24" height="6"/><path d="M3 17v4M23 17v4"/></svg>4 Bedroom SIL Home</p>
  </article>
  <article class="abs card" style="left:439px;top:739px">
    <div class="card-photo" role="img" aria-label="Photo of a red brick home with a paved driveway in Mount Druitt" style="background:linear-gradient(#9cc8ea,#a8644b 45%,#3f7a2d 70%,#c97b5c)"></div>
    <h3 class="card-title"><svg width="12" height="16" viewBox="0 0 12 16"><path d="M6 0a6 6 0 0 0-6 6c0 4.5 6 10 6 10s6-5.5 6-10a6 6 0 0 0-6-6z" fill="currentColor"/><circle cx="6" cy="6" r="2.3" fill="#fff"/></svg>Mount Druitt</h3>
    <p class="card-meta"><svg width="26" height="22" viewBox="0 0 26 22" fill="none" stroke="#f29b7a" stroke-width="1.5"><rect x="3" y="2" width="20" height="9" rx="1"/><rect x="6" y="5" width="6" height="4"/><rect x="14" y="5" width="6" height="4"/><rect x="1" y="11" width="24" height="6"/><path d="M3 17v4M23 17v4"/></svg>4 Bedroom SIL Home</p>
  </article>
  <article class="abs card" style="left:774px;top:739px">
    <div class="card-photo" role="img" aria-label="Photo of a cream rendered home with a dark roof in Casula" style="background:linear-gradient(#5fb2ec,#e6dcb8 45%,#3e6a2f 72%,#8aa94f)"></div>
    <h3 class="card-title"><svg width="12" height="16" viewBox="0 0 12 16"><path d="M6 0a6 6 0 0 0-6 6c0 4.5 6 10 6 10s6-5.5 6-10a6 6 0 0 0-6-6z" fill="currentColor"/><circle cx="6" cy="6" r="2.3" fill="#fff"/></svg>Casula</h3>
    <p class="card-meta"><svg width="26" height="22" viewBox="0 0 26 22" fill="none" stroke="#f29b7a" stroke-width="1.5"><rect x="3" y="2" width="20" height="9" rx="1"/><rect x="6" y="5" width="6" height="4"/><rect x="14" y="5" width="6" height="4"/><rect x="1" y="11" width="24" height="6"/><path d="M3 17v4M23 17v4"/></svg>4 Bedroom SIL Home</p>
  </article>

  <!-- row 2 -->
  <article class="abs card" style="left:104px;top:1111px">
    <div class="card-photo" role="img" aria-label="Photo of a cream cottage with blue shutters in Eastwood" style="background:linear-gradient(#f4f0ea,#e2d2bc 55%,#6e9a3a)"></div>
    <h3 class="card-title"><svg width="12" height="16" viewBox="0 0 12 16"><path d="M6 0a6 6 0 0 0-6 6c0 4.5 6 10 6 10s6-5.5 6-10a6 6 0 0 0-6-6z" fill="currentColor"/><circle cx="6" cy="6" r="2.3" fill="#fff"/></svg>Eastwood</h3>
    <p class="card-meta"><svg width="26" height="22" viewBox="0 0 26 22" fill="none" stroke="#f29b7a" stroke-width="1.5"><rect x="3" y="2" width="20" height="9" rx="1"/><rect x="6" y="5" width="6" height="4"/><rect x="14" y="5" width="6" height="4"/><rect x="1" y="11" width="24" height="6"/><path d="M3 17v4M23 17v4"/></svg>4 Bedroom SIL Home</p>
  </article>
  <article class="abs card" style="left:439px;top:1111px">
    <div class="card-photo" role="img" aria-label="Photo of a brick home with a double garage and palm tree in Baulkham Hills" style="background:linear-gradient(#8ec3ea,#b7a58f 50%,#4d8e33 75%,#6fae3f)"></div>
    <h3 class="card-title"><svg width="12" height="16" viewBox="0 0 12 16"><path d="M6 0a6 6 0 0 0-6 6c0 4.5 6 10 6 10s6-5.5 6-10a6 6 0 0 0-6-6z" fill="currentColor"/><circle cx="6" cy="6" r="2.3" fill="#fff"/></svg>Baulkham Hills</h3>
    <p class="card-meta"><svg width="26" height="22" viewBox="0 0 26 22" fill="none" stroke="#f29b7a" stroke-width="1.5"><rect x="3" y="2" width="20" height="9" rx="1"/><rect x="6" y="5" width="6" height="4"/><rect x="14" y="5" width="6" height="4"/><rect x="1" y="11" width="24" height="6"/><path d="M3 17v4M23 17v4"/></svg>4 Bedroom SIL Home</p>
  </article>
  <article class="abs card" style="left:774px;top:1111px">
    <div class="card-photo" role="img" aria-label="Photo of an orange brick home with a long driveway in Merrylands" style="background:linear-gradient(#9cc6ea,#c9602e 40%,#5d9b32 65%,#b7b4ad)"></div>
    <h3 class="card-title"><svg width="12" height="16" viewBox="0 0 12 16"><path d="M6 0a6 6 0 0 0-6 6c0 4.5 6 10 6 10s6-5.5 6-10a6 6 0 0 0-6-6z" fill="currentColor"/><circle cx="6" cy="6" r="2.3" fill="#fff"/></svg>Merrylands</h3>
    <p class="card-meta"><svg width="26" height="22" viewBox="0 0 26 22" fill="none" stroke="#f29b7a" stroke-width="1.5"><rect x="3" y="2" width="20" height="9" rx="1"/><rect x="6" y="5" width="6" height="4"/><rect x="14" y="5" width="6" height="4"/><rect x="1" y="11" width="24" height="6"/><path d="M3 17v4M23 17v4"/></svg>4 Bedroom SIL Home</p>
  </article>

  <!-- row 3 -->
  <article class="abs card" style="left:104px;top:1483px">
    <div class="card-photo" role="img" aria-label="Photo of a two-storey home with a green lawn in Austral" style="background:linear-gradient(#3f86d8,#8e8a86 45%,#56a72c 70%,#6cbf34)"></div>
    <h3 class="card-title"><svg width="12" height="16" viewBox="0 0 12 16"><path d="M6 0a6 6 0 0 0-6 6c0 4.5 6 10 6 10s6-5.5 6-10a6 6 0 0 0-6-6z" fill="currentColor"/><circle cx="6" cy="6" r="2.3" fill="#fff"/></svg>Austral</h3>
    <p class="card-meta"><svg width="26" height="22" viewBox="0 0 26 22" fill="none" stroke="#f29b7a" stroke-width="1.5"><rect x="3" y="2" width="20" height="9" rx="1"/><rect x="6" y="5" width="6" height="4"/><rect x="14" y="5" width="6" height="4"/><rect x="1" y="11" width="24" height="6"/><path d="M3 17v4M23 17v4"/></svg>4 Bedroom SIL Home</p>
  </article>
  <article class="abs card is-active" style="left:439px;top:1483px">
    <div class="card-photo" role="img" aria-label="Photo of a two-storey grey home with a wide garage in Marayong" style="background:linear-gradient(#7fb3e3,#7d8792 45%,#d7d6d2 75%,#9a9690)"></div>
    <h3 class="card-title"><svg width="12" height="16" viewBox="0 0 12 16"><path d="M6 0a6 6 0 0 0-6 6c0 4.5 6 10 6 10s6-5.5 6-10a6 6 0 0 0-6-6z" fill="currentColor"/><circle cx="6" cy="6" r="2.3" fill="#fff"/></svg>Marayong</h3>
    <p class="card-meta"><svg width="26" height="22" viewBox="0 0 26 22" fill="none" stroke="#f29b7a" stroke-width="1.5"><rect x="3" y="2" width="20" height="9" rx="1"/><rect x="6" y="5" width="6" height="4"/><rect x="14" y="5" width="6" height="4"/><rect x="1" y="11" width="24" height="6"/><path d="M3 17v4M23 17v4"/></svg>4 Bedroom SIL Home</p>
  </article>
</main>

<footer>
  <div class="abs site-footer"></div>
  <div class="abs footer-brand"><span class="brand-dot"></span><span class="brand-name">Tallowcrest Care</span></div>
  <ul class="abs contact-list">
    <li><svg width="16" height="12" viewBox="0 0 16 12" fill="none" stroke="#e8307a" stroke-width="1.4"><rect x="1" y="1" width="14" height="10" rx="1"/><path d="M1 1l7 6 7-6"/></svg>Email: info@tallowcrestcare.com.au</li>
    <li><svg width="16" height="16" viewBox="0 0 16 16"><path d="M3 1l3 1 1 4-2 1a9 9 0 0 0 4 4l1-2 4 1 1 3-2 2C7 15 1 9 1 3z" fill="#e8307a"/></svg>Phone: +61 0400 318 562</li>
    <li><svg width="16" height="16" viewBox="0 0 16 16" fill="none" stroke="#e8307a" stroke-width="1.4"><circle cx="8" cy="8" r="7"/><path d="M8 4v4l3 2"/></svg>Operating Hours: 9AM To 5PM Monday - Friday</li>
  </ul>
  <ul class="abs social">
    <li style="background:#6b2b83"></li>
    <li style="background:#2a62b3"></li>
    <li style="background:#1c1c1c"></li>
    <li style="background:#1b6fc4"></li>
  </ul>
  <div class="abs footer-col" style="left:617px;top:1985px">
    <h4>ACCOMMODATION</h4>
    <ul>
      <li>Supported Independent Living (SIL)</li>
      <li>Specialist Disability Accommodation (SDA)</li>
      <li>Short term Accommodation (Respite)</li>
      <li>Vacancies</li>
    </ul>
  </div>
  <div class="abs footer-col" style="left:887px;top:1985px">
    <h4>WHAT WE DO</h4>
    <ul>
      <li>In Home Care</li>
      <li>Social &amp; Community Services</li>
      <li>Therapeutic Supports</li>
      <li>Support Coordination</li>
      <li>Home Modifications</li>
    </ul>
  </div>
  <div class="abs bottom-bar">
    <p class="copy">© Copyright 2024 | Tallowcrest Care | All Rights Reserved.</p>
    <span class="code">C49</span>
    <a class="to-top" aria-label="Back to top"><svg width="10" height="7" viewBox="0 0 10 7"><path d="M0 7l5-7 5 7z" fill="#fff"/></svg></a>
  </div>
</footer>

</body>
</html>
```